Frostvale Harborline LLC

we need a business card design

Industry/Entity Type

hvac

Contact Information for Business Card

my logo

Requirements
Must have
• my logo and same colors

```html
<!DOCTYPE html>
<html lang="en">
<head>
<meta charset="utf-8">
<title>Frostvale Harborline LLC – Business Card</title>
<link rel="stylesheet" href="https://fonts.googleapis.com/css2?family=Montserrat:wght@400;500;700;800&display=swap">
<style>
  :root {
    --brand-blue: #0b5ea3;
    --brand-gold: #f4b54e;
    --gold-line: #f0a93a;
    --paper: #ffffff;
    --backdrop: #b3b3b3;
  }
  * { margin: 0; padding: 0; box-sizing: border-box; }
  html, body { width: 1200px; height: 900px; overflow: hidden; }
  body {
    background: var(--backdrop);
    font-family: "Montserrat", sans-serif;
    display: flex;
    align-items: center;
    justify-content: center;
    gap: 40px;
  }
  .card {
    position: relative;
    width: 540px;
    height: 309px;
    overflow: hidden;
    box-shadow: 0 6px 18px rgba(0,0,0,0.25);
  }
  .card-front {
    background: var(--brand-blue);
    border-bottom: 4px solid var(--brand-gold);
  }
  .front-arc {
    position: absolute;
    inset: 0;
    width: 100%;
    height: 100%;
  }
  .front-brand {
    position: absolute;
    right: 34px;
    top: 72px;
    width: 200px;
    text-align: center;
    color: var(--brand-blue);
    font-weight: 800;
    font-size: 22px;
    line-height: 1.15;
    text-transform: uppercase;
  }
  .holder {
    position: absolute;
    left: 30px;
    top: 118px;
  }
  .holder-name {
    color: var(--brand-gold);
    font-weight: 700;
    font-size: 22px;
  }
  .holder-title {
    color: var(--paper);
    font-size: 12px;
    font-weight: 500;
    margin-top: 2px;
  }
  .contact {
    position: absolute;
    left: 30px;
    bottom: 26px;
    color: var(--paper);
    font-size: 11.5px;
    line-height: 1.55;
  }
  .contact-address { margin-bottom: 10px; }
  .contact-row { display: flex; align-items: center; gap: 8px; }
  .contact-row svg { width: 12px; height: 12px; flex: none; }
  .card-back {
    background: var(--brand-gold);
    display: flex;
    align-items: center;
    justify-content: center;
  }
  .back-brand {
    color: var(--brand-blue);
    font-weight: 800;
    font-size: 34px;
    line-height: 1.15;
    text-align: center;
    text-transform: uppercase;
  }
</style>
</head>
<body>
  <section class="card card-front">
    <svg class="front-arc" viewBox="0 0 540 309" aria-hidden="true">
      <path d="M300 0 C250 80 250 190 330 240 C400 280 480 260 540 220 L540 0 Z" fill="var(--paper)"/>
      <path d="M290 10 C236 100 246 210 330 246 C400 276 480 262 540 226" fill="none" stroke="var(--gold-line)" stroke-width="5"/>
    </svg>
    <div class="front-brand">Frostvale Harborline LLC</div>

    <div class="holder">
      <div class="holder-name">Daniel Reyes</div>
      <div class="holder-title">Managing Director</div>
    </div>

    <div class="contact">
      <div class="contact-address">48 Harbor Lane,<br>Riverton, NY 13500</div>
      <div class="contact-row">
        <svg viewBox="0 0 12 12"><rect x="2.5" y="0.5" width="7" height="11" rx="1.5" fill="none" stroke="var(--brand-gold)" stroke-width="1.2"/></svg>
        +1 (555) 014-2290
      </div>
      <div class="contact-row">
        <svg viewBox="0 0 12 12"><rect x="0.5" y="2" width="11" height="8" fill="var(--brand-gold)"/><path d="M0.5 2 L6 7 L11.5 2" fill="none" stroke="var(--brand-blue)" stroke-width="1"/></svg>
        hello@frostvaleharbor.com
      </div>
      <div class="contact-row">
        <svg viewBox="0 0 12 12"><circle cx="6" cy="6" r="5.5" fill="var(--brand-gold)"/><path d="M0.5 6 H11.5 M6 0.5 C3 3.5 3 8.5 6 11.5 M6 0.5 C9 3.5 9 8.5 6 11.5" fill="none" stroke="var(--brand-blue)" stroke-width="0.8"/></svg>
        www.frostvaleharbor.com
      </div>
    </div>
  </section>

  <section class="card card-back">
    <div class="back-brand">Frostvale<br>Harborline LLC</div>
  </section>
</body>
</html>
```